Power Point Template Vierklang sustainability consulting

(find english description below)
We are a small German start-up that offers sustainability consulting. For presentations of results, our company presentation, proposals, lectures, etc., we need a PowerPoint template that matches our logo. We come from classic management consulting / strategy consulting and also deal with facts and figures in sustainability consulting. Therefore, the template should not be too fancy and should not only consist of photos. But it shouldn't be a completely sober template either. Our logo with the green leaves for sustainability (three leaves for VIERklang) and the white bar chart (with the dynamic swing upwards) reflects our attitude well, where we see ourselves on the range from playful to sober and classic to modern.

It might be nice for the template to include the shape of one of the leaves (from the logo). Also, the logo should appear in a corner of each slide. The colors from the logo (see appendix) should be partially reflected in the presentation. We can also imagine a gold-brown tone (see website www.vierklang-beratung.de) or a coral tone as a contrast. (Attention - the website is not final yet).

For a first suggestion, it is sufficient to suggest three to four slides (cover sheet, chapter/separation slide, text slide, data slide). We will then mark drafts that we like. In total, we would then need about 6-10 more slide templates, e.g. about us, team, slide for a statement, 2-3 data charts (pie, bar, column), top 3 - 5 list, timeline, contact (more slides are welcome ).

We are a small German start-up offering sustainability consulting. We need a power point template for result presentations, our company presentation, proposals, lectures etc. The template should be aligned with our logo. Our background lies in classic management consulting / strategy consulting and we also deal with facts and figures in sustainability consulting. Therefore, the template should not be too playful and not only consist of photos. But it should also not be a completely clear template. Our logo with the green leaves for sustainability (three leaves for VIERklang) and the white bar chart (with the dynamic upward swing) reflects our attitude well, where we see ourselves on the range from playful to down-to-earth and classic to modern .

For the template, it might be nice to incorporate the shape of one of the leaves (from the logo). Also, the logo should show up in one corner on each slide. Some of the colors from the logo (see attachment) should be reflected in the presentation. We could also think of a gold-brown tone (see website www.vierklang-beratung.de) or a coral tone for contrast. (Attention - the website is not final yet).

For a first proposal it is quite sufficient to suggest us three to four slides (cover page, chapter/separation slide, text slide, data slide). We will then mark the drafts that we like. In total we would need about 6-10 more slide templates, eg About us, Team, slide for a statement, 2-3 data charts (pie, bar, column), Top 3 - 5 List, Timeline, Contact (more slides are welcome).

Target Market(s)

Corporations, large companies and SMEs

Industry/Entity Type

Unternehmensberatung, Nachhaltigkeitsberatung

Font styles to use
Sans Serif
Other font styles liked:
• Calibri

Colors
00AB8E
00BBA5
67D7C9
C6EFE9
E9F9F6

Requirements
Must have
• see description (e.g. the colors of our logo)
Nice to have
• see description (e.g. elements of the logo included)
Should not have
• see description

```html
<!DOCTYPE html>
<html lang="en">
<head>
<meta charset="utf-8">
<title>Vierklang Consulting – Presentation Template</title>
<link href="https://fonts.googleapis.com/css2?family=Open+Sans:wght@400;600;700&display=swap" rel="stylesheet">
<style>
:root{
  --canvas:#e6e7ea;
  --white:#ffffff;
  --green-dark:#3f6d14;
  --green:#4f8222;
  --green-light:#8bb936;
  --gold:#b09650;
  --gold-light:#d6c79a;
  --text:#5b5b5b;
  --text-soft:#7a7a7a;
  --grid:#e4e4e4;
}
*{margin:0;padding:0;box-sizing:border-box}
html,body{width:1200px;height:4051px;overflow:hidden}
body{background:var(--canvas);font-family:"Open Sans",Calibri,sans-serif;color:var(--text);position:relative}
.slide{position:absolute;left:77px;width:1046px;height:588px;background:var(--white);overflow:hidden;box-shadow:0 6px 18px rgba(0,0,0,.14)}
.abs{position:absolute}
.logo{position:absolute;display:flex;align-items:center;gap:10px;font-size:40px;font-weight:400;line-height:1}
.logo .dot{width:34px;height:34px;border-radius:50%}
.logo-corner{right:60px;top:30px;color:#6a6a6a}
.logo-corner .dot{background:var(--green-light)}

/* cover */
.cover{top:88px;background:linear-gradient(120deg,#3f7a16 0%,#5e9627 55%,#86b738 100%)}
.cover .logo{left:61px;top:30px;color:var(--white)}
.cover .logo .dot{background:var(--white)}
.cover-title{left:58px;top:222px;font-size:32px;font-weight:700;color:var(--white);line-height:1.3}
.cover-rule{left:58px;top:318px;width:80px;height:2px;background:var(--white)}
.cover-lead{left:58px;top:339px;width:370px;font-size:14.5px;line-height:24px;color:var(--white)}
.cover-photo{left:470px;top:110px;width:540px;height:400px;border-radius:40px;background:linear-gradient(135deg,#b9c9a6 0%,#d8ddd2 50%,#8d9c84 100%)}

/* about */
.about{top:738px}
.about-band{left:0;top:0;width:184px;height:100%;background:var(--gold)}
.about-photo{left:64px;top:93px;width:458px;height:403px;border-radius:46px;background:linear-gradient(135deg,#dfe3e4 0%,#b9c0c4 45%,#2f3846 80%,#1f2633 100%)}
.section-title{font-size:31px;font-weight:700;color:var(--gold)}
.about-title{left:583px;top:151px}
.about-copy{left:583px;top:214px;width:403px;font-size:13.5px;line-height:23px;text-align:justify;color:var(--text-soft)}
.about-copy p+p{margin-top:13px}

/* headers */
.head-band{left:0;top:0}
.head-title{left:60px;top:20px;font-size:31px;font-weight:700;color:var(--white)}

/* team */
.team{top:1397px}
.member{top:173px;width:263px;height:318px;background:var(--white);box-shadow:0 3px 12px rgba(0,0,0,.16);text-align:center;padding:36px 18px 0}
.member .avatar{width:88px;height:88px;border-radius:50%;margin:0 auto;background:radial-gradient(circle at 50% 40%,#c9a58d 0%,#6f5848 70%,#dcdcdc 100%);border:2px solid #eee}
.member h3{margin-top:33px;font-size:15px;font-weight:700;color:var(--green-dark)}
.member .role{margin-top:4px;font-size:12px;color:var(--gold)}
.member p{margin-top:12px;font-size:10.5px;line-height:18px;color:var(--text-soft)}

/* data */
.data{top:2056px}
.chart{left:40px;top:132px}
.chart text{font-family:"Open Sans",Calibri,sans-serif}
.bullets{left:694px;top:150px;width:300px;list-style:none}
.bullets li{position:relative;padding-left:26px;font-size:12px;line-height:21px;color:var(--text-soft);margin-bottom:11px}
.bullets li svg{position:absolute;left:0;top:4px}

/* timeline */
.timeline{top:2715px}
.year{top:176px;width:240px;text-align:center;font-size:17px;font-weight:700}
.step{top:219px;width:240px;height:241px;border:2px dashed var(--green)}
.step-inner{position:absolute;left:20px;top:20px;right:20px;bottom:20px;color:var(--white);text-align:center;padding:30px 12px 0}
.step-inner h4{margin-top:14px;font-size:12.5px;font-weight:700}
.step-inner p{margin-top:8px;font-size:10.5px;line-height:18px}
.arrow{top:334px}

/* contact */
.contact{top:3374px}
.contact-photo{left:0;top:0}
.thanks{left:596px;top:218px;font-size:42px;font-weight:700;color:var(--gold)}
.contact-list{left:596px;top:308px;list-style:none}
.contact-list li{display:flex;align-items:flex-start;gap:16px;font-size:14px;line-height:27px;color:#555;margin-bottom:17px}
.contact-list svg{flex:none;margin-top:3px}
</style>
</head>
<body>

<!-- Cover -->
<section class="slide cover">
  <div class="logo"><span class="dot"></span>Vierklang</div>
  <h1 class="abs cover-title">VIERKLANG<br>CONSULTING</h1>
  <div class="abs cover-rule"></div>
  <p class="abs cover-lead">At Vierklang Consulting, we support companies and public institutions in anchoring and expanding sustainability in their companies</p>
  <div class="abs cover-photo" role="img" aria-label="Photo of a desk with laptop and potted plant"></div>
</section>

<!-- About us -->
<section class="slide about">
  <div class="abs about-band"></div>
  <div class="abs about-photo" role="img" aria-label="Photo of two colleagues reviewing work at an office desk"></div>
  <div class="logo logo-corner"><span class="dot"></span>Vierklang</div>
  <h2 class="abs section-title about-title">ABOUT US</h2>
  <div class="abs about-copy">
    <p>At Vierklang Consulting, we support companies and public institutions in anchoring and expanding sustainability in their companies – with the aim of making them more attractive, future-proof and successful.</p>
    <p>Regardless of whether you are still at the very beginning of the process of implementing sustainability aspects in your company or whether sustainable management is already anchored in the corporate culture - we will be happy to support you with our modular offers</p>
  </div>
</section>

<!-- Team -->
<section class="slide team">
  <svg class="abs head-band" width="660" height="90" viewBox="0 0 660 90" aria-hidden="true">
    <polygon points="0,0 650,0 610,88 0,88" fill="var(--gold-light)"/>
    <polygon points="0,0 640,0 602,80 0,80" fill="var(--gold)"/>
  </svg>
  <h2 class="abs head-title">OUR TEAM</h2>
  <div class="logo logo-corner"><span class="dot"></span>Vierklang</div>

  <article class="abs member" style="left:103px">
    <div class="avatar" role="img" aria-label="Portrait photo of Dr. Mara Lindqvist"></div>
    <h3>DR. MARA LINDQVIST</h3>
    <div class="role">Managing Partner</div>
    <p>Mara is co-founder and managing director of Vierklang Consulting GmbH. She has a high level of analytical comprehension, thinks very far ahead and always keeps an overview of the essential issues.</p>
  </article>
  <article class="abs member" style="left:392px">
    <div class="avatar" role="img" aria-label="Portrait photo of Dr. Petra Holm"></div>
    <h3>DR. PETRA HOLM</h3>
    <div class="role">Managing Partner</div>
    <p>Petra is co-founder and managing director of Vierklang Consulting GmbH. She is very good at systematically grasping complex issues and reducing them to the essentials. She thinks with foresight and develops target</p>
  </article>
  <article class="abs member" style="left:681px">
    <div class="avatar" role="img" aria-label="Portrait photo of Dr. Clara Weidenfeld"></div>
    <h3>DR. CLARA WEIDENFELD</h3>
    <div class="role">Managing Partner</div>
    <p>Clara is co-founder and managing director of Vierklang Consulting GmbH. She always manages to react pragmatically and solution-oriented to changing customer requirements in dynamic project environments</p>
  </article>
</section>

<!-- Data -->
<section class="slide data">
  <svg class="abs head-band" width="660" height="90" viewBox="0 0 660 90" aria-hidden="true">
    <polygon points="0,0 650,0 610,88 0,88" fill="var(--gold-light)"/>
    <polygon points="0,0 640,0 602,80 0,80" fill="var(--gold)"/>
  </svg>
  <h2 class="abs head-title">OUR DATA</h2>
  <div class="logo logo-corner"><span class="dot"></span>Vierklang</div>

  <svg class="abs chart" width="620" height="420" viewBox="0 0 620 420" role="img" aria-label="Column chart comparing two series per weekday">
    <g stroke="var(--grid)" stroke-width="1">
      <line x1="45" y1="18" x2="605" y2="18"/>
      <line x1="45" y1="366" x2="605" y2="366"/>
      <line x1="45" y1="18" x2="45" y2="366"/>
      <line x1="125" y1="18" x2="125" y2="366"/>
      <line x1="205" y1="18" x2="205" y2="366"/>
      <line x1="285" y1="18" x2="285" y2="366"/>
      <line x1="365" y1="18" x2="365" y2="366"/>
      <line x1="445" y1="18" x2="445" y2="366"/>
      <line x1="525" y1="18" x2="525" y2="366"/>
      <line x1="605" y1="18" x2="605" y2="366"/>
    </g>
    <g font-size="11" font-weight="600" fill="#444" text-anchor="end">
      <text x="30" y="22">120</text><text x="30" y="80">100</text><text x="30" y="138">80</text>
      <text x="30" y="196">60</text><text x="30" y="254">40</text><text x="30" y="312">20</text><text x="30" y="370">0</text>
    </g>
    <g>
      <rect x="67" y="76" width="16" height="290" fill="var(--green)"/><rect x="89" y="105" width="16" height="261" fill="var(--gold)"/>
      <rect x="147" y="105" width="16" height="261" fill="var(--green)"/><rect x="169" y="134" width="16" height="232" fill="var(--gold)"/>
      <rect x="227" y="221" width="16" height="145" fill="var(--green)"/><rect x="249" y="76" width="16" height="290" fill="var(--gold)"/>
      <rect x="307" y="76" width="16" height="290" fill="var(--green)"/><rect x="329" y="192" width="16" height="174" fill="var(--gold)"/>
      <rect x="387" y="76" width="16" height="290" fill="var(--green)"/><rect x="409" y="105" width="16" height="261" fill="var(--gold)"/>
      <rect x="467" y="192" width="16" height="174" fill="var(--green)"/><rect x="489" y="148" width="16" height="218" fill="var(--gold)"/>
      <rect x="547" y="221" width="16" height="145" fill="var(--green)"/><rect x="569" y="76" width="16" height="290" fill="var(--gold)"/>
    </g>
    <g font-size="11" font-weight="700" fill="#333" text-anchor="middle">
      <text x="75" y="68">100</text><text x="97" y="97">90</text>
      <text x="155" y="97">90</text><text x="177" y="126">80</text>
      <text x="235" y="213">50</text><text x="257" y="68">100</text>
      <text x="315" y="68">100</text><text x="337" y="184">60</text>
      <text x="395" y="68">100</text><text x="417" y="97">90</text>
      <text x="475" y="184">60</text><text x="497" y="140">75</text>
      <text x="555" y="213">50</text><text x="577" y="68">100</text>
    </g>
    <g font-size="12" font-weight="700" fill="#333" text-anchor="middle">
      <text x="86" y="392">Sun</text><text x="166" y="392">Mon</text><text x="246" y="392">Tue</text>
      <text x="326" y="392">Wed</text><text x="406" y="392">Thu</text><text x="486" y="392">Fri</text><text x="566" y="392">Sat</text>
    </g>
  </svg>

  <ul class="abs bullets">
    <li><svg width="14" height="14" viewBox="0 0 14 14" aria-hidden="true"><circle cx="7" cy="7" r="7" fill="var(--green-light)"/><path d="M3.8 7.2 6 9.3 10.2 4.9" stroke="#fff" stroke-width="1.8" fill="none"/></svg>Lorem ipsum dolor sit consectetur adipiscing elit, sed do eiusmod tempor incididunt ut labore et dolore magna aliqua.</li>
    <li><svg width="14" height="14" viewBox="0 0 14 14" aria-hidden="true"><circle cx="7" cy="7" r="7" fill="var(--green-light)"/><path d="M3.8 7.2 6 9.3 10.2 4.9" stroke="#fff" stroke-width="1.8" fill="none"/></svg>Lorem ipsum dolor sit consectetur adipiscing elit, sed do eiusmod</li>
    <li><svg width="14" height="14" viewBox="0 0 14 14" aria-hidden="true"><circle cx="7" cy="7" r="7" fill="var(--green-light)"/><path d="M3.8 7.2 6 9.3 10.2 4.9" stroke="#fff" stroke-width="1.8" fill="none"/></svg>Lorem ipsum dolor sit consectetur adipiscing elit, sed do eiusmod tempor incididunt ut labore et dolore magna aliqua.</li>
    <li><svg width="14" height="14" viewBox="0 0 14 14" aria-hidden="true"><circle cx="7" cy="7" r="7" fill="var(--green-light)"/><path d="M3.8 7.2 6 9.3 10.2 4.9" stroke="#fff" stroke-width="1.8" fill="none"/></svg>Lorem ipsum dolor sit consectetur adipiscing elit, sed do eiusmod</li>
    <li><svg width="14" height="14" viewBox="0 0 14 14" aria-hidden="true"><circle cx="7" cy="7" r="7" fill="var(--green-light)"/><path d="M3.8 7.2 6 9.3 10.2 4.9" stroke="#fff" stroke-width="1.8" fill="none"/></svg>Lorem ipsum dolor sit consectetur adipiscing elit, sed do eiusmod tempor incididunt ut labore et dolore magna aliqua.</li>
    <li><svg width="14" height="14" viewBox="0 0 14 14" aria-hidden="true"><circle cx="7" cy="7" r="7" fill="var(--green-light)"/><path d="M3.8 7.2 6 9.3 10.2 4.9" stroke="#fff" stroke-width="1.8" fill="none"/></svg>Lorem ipsum dolor sit consectetur adipiscing elit, sed do eiusmod</li>
  </ul>
</section>

<!-- Timeline -->
<section class="slide timeline">
  <svg class="abs head-band" width="660" height="90" viewBox="0 0 660 90" aria-hidden="true">
    <polygon points="0,0 650,0 610,88 0,88" fill="var(--gold-light)"/>
    <polygon points="0,0 640,0 602,80 0,80" fill="var(--gold)"/>
  </svg>
  <h2 class="abs head-title">OUR TIMELINE</h2>
  <div class="logo logo-corner"><span class="dot"></span>Vierklang</div>

  <div class="abs year" style="left:116px;color:var(--green-dark)">2021</div>
  <div class="abs year" style="left:402px;color:var(--green-light)">2022</div>
  <div class="abs year" style="left:688px;color:var(--gold)">2023</div>

  <div class="abs step" style="left:116px;border-color:var(--green-dark)">
    <div class="step-inner" style="background:var(--green-dark)">
      <svg width="40" height="40" viewBox="0 0 40 40" aria-hidden="true" fill="none" stroke="#fff" stroke-width="2"><rect x="4" y="5" width="26" height="22" rx="2"/><circle cx="26" cy="25" r="7"/><line x1="31" y1="30" x2="37" y2="36"/><line x1="9" y1="12" x2="22" y2="12"/><line x1="9" y1="18" x2="17" y2="18"/></svg>
      <h4>ORIENTATION</h4>
      <p>Understand the legal framework and possible fields of action for your company.</p>
    </div>
  </div>
  <div class="abs step" style="left:402px;border-color:var(--green-light)">
    <div class="step-inner" style="background:var(--green-light)">
      <svg width="40" height="40" viewBox="0 0 40 40" aria-hidden="true" fill="none" stroke="#fff" stroke-width="2"><rect x="8" y="4" width="24" height="30" rx="2"/><line x1="13" y1="12" x2="27" y2="12"/><line x1="13" y1="18" x2="27" y2="18"/><path d="M13 26 17 29 27 22"/></svg>
      <h4>STRATEGY</h4>
      <p>Develop a sustainability strategy, define goals and select suitable measures.</p>
    </div>
  </div>
  <div class="abs step" style="left:688px;border-color:var(--gold)">
    <div class="step-inner" style="background:var(--gold)">
      <svg width="40" height="40" viewBox="0 0 40 40" aria-hidden="true" fill="none" stroke="#fff" stroke-width="2"><rect x="4" y="10" width="20" height="24" rx="2"/><line x1="9" y1="17" x2="19" y2="17"/><line x1="9" y1="23" x2="19" y2="23"/><circle cx="30" cy="12" r="5"/><path d="M22 34 C22 24 38 24 38 34"/></svg>
      <h4>IMPLEMENTATION</h4>
      <p>Anchor the sustainability strategy effectively in your business processes and corporate culture.</p>
    </div>
  </div>

  <svg class="abs arrow" style="left:356px" width="46" height="14" viewBox="0 0 46 14" aria-hidden="true"><line x1="0" y1="7" x2="38" y2="7" stroke="var(--green-dark)" stroke-width="2"/><polygon points="36,1 46,7 36,13" fill="var(--green-dark)"/></svg>
  <svg class="abs arrow" style="left:642px" width="46" height="14" viewBox="0 0 46 14" aria-hidden="true"><line x1="0" y1="7" x2="38" y2="7" stroke="var(--green-light)" stroke-width="2"/><polygon points="36,1 46,7 36,13" fill="var(--green-light)"/></svg>
</section>

<!-- Contact -->
<section class="slide contact">
  <svg class="abs contact-photo" width="680" height="588" viewBox="0 0 680 588" role="img" aria-label="Photo of a businessman using a tablet beside a laptop">
    <defs>
      <linearGradient id="contactPhoto" x1="0" y1="0" x2="1" y2="1">
        <stop offset="0" stop-color="#a9ab6e"/>
        <stop offset=".45" stop-color="#5d4d3c"/>
        <stop offset="1" stop-color="#c9c6bf"/>
      </linearGradient>
    </defs>
    <path d="M0 0 H668 C560 120 420 200 441 300 C455 390 530 470 540 588 H0 Z" fill="url(#contactPhoto)"/>
  </svg>
  <div class="logo logo-corner"><span class="dot"></span>Vierklang</div>
  <h2 class="abs thanks">THANK YOU</h2>
  <ul class="abs contact-list">
    <li><svg width="22" height="22" viewBox="0 0 22 22" aria-hidden="true"><path d="M5 2 8 2 9.5 7 7.5 8.5C8.5 11 11 13.5 13.5 14.5L15 12.5 20 14V17C20 18.5 18.5 20 17 20 9 19.5 2.5 13 2 5 2 3.5 3.5 2 5 2Z" fill="var(--green)"/></svg>+49 (0) 6221 – 480 3927</li>
    <li><svg width="22" height="22" viewBox="0 0 22 22" aria-hidden="true" fill="none" stroke="var(--green)" stroke-width="1.8"><circle cx="11" cy="11" r="9"/><ellipse cx="11" cy="11" rx="4" ry="9"/><line x1="2" y1="11" x2="20" y2="11"/></svg>www.vierklang-beratung.de</li>
    <li><svg width="22" height="22" viewBox="0 0 22 22" aria-hidden="true" fill="none" stroke="var(--green)" stroke-width="1.8"><rect x="2" y="5" width="18" height="13"/><path d="M2 5 11 12 20 5"/></svg>info@vierklang-beratung.de</li>
    <li><svg width="22" height="22" viewBox="0 0 22 22" aria-hidden="true"><path d="M11 1C7 1 4 4 4 8c0 5 7 12 7 12s7-7 7-12c0-4-3-7-7-7Z" fill="var(--green)"/><circle cx="11" cy="8" r="2.6" fill="#fff"/></svg><span>Lindenhof Business Park, Gartenstrasse 14<br>64283 Darmstadt / Hessen</span></li>
  </ul>
</section>

</body>
</html>
```